Varelko App for Smart Devices IoT WiFi Electronic

Varelko is a siren manufacturer. This application is used for the company's products that have a Wi-Fi connection and an internet connection, which can be configured and activated remotely through this application. In addition, this application is used to activate the siren at specific times for the start and end of shifts in companies and schools. Users will be siren installers and IT or HR managers.
In addition to activating motorized sirens timers, some siren models have speakers and allow you to play TTS (text to speech) audio, audio recorded by the user on the phone and upload audio (mp3) with playlist programming with start and end times.
Application screens: home with dashboard (one dashboard for each category). Device categories: timers, speakers, motorized siren. Screen for requesting evaluation in the Play Store. Screen for registering the user profile. Screen for registering devices according to their category (timers, speakers, motorized siren). Screen for registering device groups. Screen for pairing the device on the client's Wi-Fi network. Screen for registering activation times. Screen for uploading MP3 audios. Screen for registering playlists with audio selection, start and end times. Screen for recording audio for later sending to the speakers. Screen for converting text to speech and sending to the speakers. It is important to have a time picker with the day of the week to program the activation times and playlist.

Target Market(s)

Schools, Companies and Stores.

Industry/Entity Type

IoT

Font styles to use
Sans Serif
Other font styles liked:
• roboto

Colors
FFC000
F8CF3A
FAE287
FDF2CF
FEFAEE

Requirements
Must have
• time picker with weekdays for timer programming feature.
Nice to have
• app review request screen on play store

```html
<!DOCTYPE html>
<html lang="en">
<head>
<meta charset="utf-8">
<title>Varelko App UI</title>
<link href="https://fonts.googleapis.com/css2?family=Roboto:wght@400;500;700&display=swap" rel="stylesheet">
<style>
:root{
  --amber:#FFC000;
  --amber-soft:#F8CF3A;
  --amber-pale:#FAE287;
  --cream:#FDF2CF;
  --paper:#F7F7F7;
  --ink:#1B1B1B;
  --muted:#8E8E8E;
  --key-orange:#F29A00;
}
*{box-sizing:border-box;margin:0;padding:0}
html,body{width:730px;height:1200px;overflow:hidden}
body{font-family:'Roboto',sans-serif;color:var(--ink);background:#3a3a3a}
.canvas{width:730px;height:1200px;overflow:hidden;position:relative}
.stage{position:absolute;left:0;top:0;width:1500px;height:2464px;transform:scale(0.48667);transform-origin:0 0;
  background:linear-gradient(180deg,#666 0%,#474747 45%,#2b2b2b 100%)}
.screen{position:absolute;width:256px;height:553px;background:var(--paper);overflow:hidden}
.status{position:absolute;left:0;top:0;width:100%;height:28px;background:var(--amber);display:flex;justify-content:space-between;align-items:center;padding:0 12px 0 22px;font-size:10px;font-weight:500}
.status svg{width:38px;height:10px}
.brand{position:absolute;left:0;right:0;text-align:center;color:var(--amber);font-weight:700}
.title{position:absolute;left:0;right:0;top:38px;text-align:center;font-size:15px;font-weight:500}
.close{position:absolute;right:12px;top:37px;width:20px;height:20px}
.label{position:absolute;left:44px;font-size:10px;font-weight:500}
.field{position:absolute;left:32px;width:194px;height:23px;border:2px solid var(--amber);border-radius:12px;font-size:8px;color:var(--muted);padding-left:11px;line-height:19px;background:#fff}
.select{position:absolute;height:23px;border:2px solid var(--amber);border-radius:12px;font-size:10px;font-weight:500;line-height:19px;background:#fff;display:flex;justify-content:center;align-items:center}
.select.left{justify-content:flex-start;padding-left:14px}
.select .caret{position:absolute;right:12px;top:6px;width:9px;height:7px}
.btn{position:absolute;left:63px;width:130px;height:32px;border-radius:16px;background:var(--amber);font-size:13px;font-weight:500;text-align:center;line-height:32px}
.divider{position:absolute;left:0;width:100%;height:10px;display:flex;align-items:center;gap:6px;font-size:9px;font-weight:700}
.divider::before,.divider::after{content:"";flex:1;border-top:1px dashed #888}
.social{position:absolute;height:23px;border:2px solid var(--amber);border-radius:12px;font-size:8px;font-weight:500;display:flex;align-items:center;justify-content:center;gap:6px;background:#fff}
.social .dot{width:10px;height:10px;border-radius:50%;background:#555}
.icon{position:absolute;color:var(--ink)}
.plus{position:absolute;left:195px;width:32px;height:32px;border-radius:50%;background:var(--amber)}
.plus svg{width:32px;height:32px}
.tabbar{position:absolute;left:0;top:493px;width:256px;height:60px}
.time-card{position:absolute;left:42px;width:180px;height:70px;border:2px solid var(--amber);border-radius:14px;text-align:center;background:#fff}
.time-card .big{font-size:50px;font-weight:700;line-height:52px;margin-top:2px}
.time-card .big small{font-size:16px;font-weight:500}
.time-card .days{font-size:10px;color:var(--muted);margin-top:-4px}
.picker{position:absolute;left:38px;top:104px;width:180px;height:180px;border:2px solid var(--amber);border-radius:14px;background:#fff}
.picker .digits{position:absolute;left:16px;top:2px;font-size:40px;font-weight:500}
.picker .digits span{background:#e4e4e4;border-radius:3px}
.picker .ampm{position:absolute;left:136px;top:14px;font-size:7px;font-weight:700;line-height:8px}
.picker svg{position:absolute;left:32px;top:56px;width:116px;height:116px}
.caption{position:absolute;left:0;right:0;text-align:center;font-size:10px;font-weight:500}
.days-row{position:absolute;left:27px;top:316px;display:flex;gap:4px}
.chip{width:25px;height:18px;border:1.5px solid var(--amber);border-radius:9px;font-size:8px;font-weight:500;text-align:center;line-height:15px;background:#fff}
.chip.on{background:var(--amber)}
.glow{position:absolute;left:66px;width:124px;height:124px;border-radius:50%;
  background:radial-gradient(circle at 50% 40%,var(--amber-soft),var(--amber) 70%);box-shadow:0 0 28px 10px var(--amber-pale);text-align:center}
.glow svg{width:68px;height:68px;margin-top:18px}
.glow p{font-size:8px;color:#6a4d00}
.tile{position:absolute;top:324px;width:52px;height:50px;border-radius:7px;background:var(--amber);text-align:center;font-size:7px}
.tile svg{width:28px;height:28px;margin-top:5px}
.wave{position:absolute;left:22px;top:282px;width:214px;height:16px}
.file{position:absolute;left:0;right:0;top:304px;text-align:center;font-size:7px;color:var(--muted)}
.browse{position:absolute;left:40px;top:241px;width:174px;height:23px;border:2px solid var(--amber);border-radius:12px;font-size:9px;color:var(--muted);text-align:center;line-height:19px;background:#fff}
.browse svg{position:absolute;right:8px;top:4px;width:11px;height:11px}
.mic-ring{position:absolute;left:91px;top:137px;width:74px;height:74px;border-radius:50%;background:var(--amber);border:3px solid #fff;box-shadow:0 0 0 2px var(--amber)}
.mic-ring svg{width:44px;height:44px;margin:12px 0 0 12px}
.note{position:absolute;left:0;right:0;top:212px;text-align:center;font-size:7px;color:var(--muted)}
.textbox{position:absolute;left:31px;top:160px;width:195px;height:140px;border:1.5px dashed var(--amber);padding:6px 8px;font-size:10px;line-height:12px}
.keyboard{position:absolute;left:0;top:335px;width:256px;height:218px;background:var(--amber)}
.suggest{display:flex;height:28px;font-size:10px;align-items:center;background:var(--amber-soft)}
.suggest span{flex:1;text-align:center}
.suggest .pick{background:var(--key-orange);height:24px;line-height:24px;margin:0 2px 0 3px;border-radius:3px}
.krow{display:flex;justify-content:center;gap:3px;margin-top:7px}
.key{width:22px;height:27px;background:#fff;border-radius:4px;font-size:15px;text-align:center;line-height:25px;box-shadow:0 1px 0 rgba(0,0,0,.25)}
.key.fn{background:var(--key-orange);width:30px;font-size:10px}
.key.wide{width:62px;font-size:10px;line-height:27px}
.key.space{width:124px;font-size:10px;line-height:27px}
.kbottom{position:absolute;left:0;top:188px;width:100%;height:30px}
.headline{position:absolute;left:745px;width:600px;top:962px;text-align:center;font-size:44px;font-weight:500;color:#e0e0e0}
.hero-name{position:absolute;left:690px;width:770px;top:1050px;text-align:center;font-size:200px;font-weight:700;line-height:220px;color:var(--amber)}
</style>
</head>
<body>
<svg width="0" height="0" style="position:absolute" aria-hidden="true">
  <defs>
    <symbol id="i-status" viewBox="0 0 38 10"><rect x="0" y="6" width="2" height="3" fill="#222"/><rect x="3" y="4" width="2" height="5" fill="#222"/><rect x="6" y="2" width="2" height="7" fill="#222"/><path d="M13 4a6 6 0 0 1 8 0M15 6a3 3 0 0 1 4 0" stroke="#222" stroke-width="1.4" fill="none"/><circle cx="17" cy="8" r="1" fill="#222"/><rect x="25" y="2" width="11" height="6" rx="1.5" fill="#222"/></symbol>
    <symbol id="i-timer" viewBox="0 0 24 24" fill="none" stroke="currentColor" stroke-width="2" stroke-linecap="round"><circle cx="12" cy="14" r="8"/><path d="M12 14V10M9 3h6M12 3v3M19 6l-1.5 1.5"/></symbol>
    <symbol id="i-siren" viewBox="0 0 24 24" fill="none" stroke="currentColor" stroke-width="2" stroke-linecap="round"><path d="M6 17v-4a6 6 0 0 1 12 0v4"/><rect x="4" y="17" width="16" height="4" rx="1"/><path d="M12 2.5v2M4.5 5l1.5 1.5M19.5 5L18 6.5M12 13l2.5-2.5"/></symbol>
    <symbol id="i-speaker" viewBox="0 0 24 24" fill="none" stroke="currentColor" stroke-width="2" stroke-linejoin="round" stroke-linecap="round"><path d="M3 9h4l6-5v16l-6-5H3z"/><path d="M16 9a4 4 0 0 1 0 6M18.5 6.5a7.5 7.5 0 0 1 0 11"/></symbol>
    <symbol id="i-mic" viewBox="0 0 24 24" fill="none" stroke="currentColor" stroke-width="2" stroke-linecap="round"><rect x="9" y="2" width="6" height="12" rx="3" fill="currentColor"/><path d="M5.5 11a6.5 6.5 0 0 0 13 0M12 17.5V21M9 21h6"/></symbol>
    <symbol id="i-note" viewBox="0 0 24 24"><path d="M8 18V6l12-3v13" fill="none" stroke="currentColor" stroke-width="2.4"/><path d="M8 6l12-3v4L8 10z" fill="currentColor"/><circle cx="5.5" cy="18" r="3" fill="currentColor"/><circle cx="17.5" cy="16" r="3" fill="currentColor"/></symbol>
    <symbol id="i-tts" viewBox="0 0 24 24" fill="none" stroke="currentColor" stroke-width="1.8" stroke-linejoin="round" stroke-linecap="round"><path d="M3 4h9l3 3v14H3z"/><path d="M6 10h6M6 13h6M6 16h4"/><path d="M15 10l3-2.5v9L15 14" fill="currentColor"/><path d="M20 9a3.5 3.5 0 0 1 0 6M21.5 6.5a7 7 0 0 1 0 11"/></symbol>
    <symbol id="i-plus" viewBox="0 0 32 32"><path d="M16 8v16M8 16h16" stroke="#1B1B1B" stroke-width="2.6" stroke-linecap="round"/></symbol>
    <symbol id="i-close" viewBox="0 0 20 20"><path d="M3 3l14 14M17 3L3 17" stroke="#1B1B1B" stroke-width="2.6" stroke-linecap="round"/></symbol>
    <symbol id="i-caret" viewBox="0 0 10 7"><path d="M0 0h10L5 7z" fill="#1B1B1B"/></symbol>
    <symbol id="i-upload" viewBox="0 0 12 12" fill="none" stroke="#666" stroke-width="1.2"><path d="M6 8V1M3 4l3-3 3 3M1 8v3h10V8"/></symbol>
    <pattern id="bars" width="12" height="16" patternUnits="userSpaceOnUse"><rect x="0" y="5" width="1.3" height="6" fill="#777"/><rect x="3" y="1" width="1.3" height="14" fill="#777"/><rect x="6" y="6" width="1.3" height="4" fill="#777"/><rect x="9" y="3" width="1.3" height="10" fill="#777"/></pattern>
    <symbol id="i-wave" viewBox="0 0 214 16"><path d="M0 2l10 6-10 6z" fill="#888"/><rect x="18" y="0" width="170" height="16" fill="url(#bars)"/><text x="191" y="11" font-size="8" fill="#888" font-family="Roboto,sans-serif">2:09</text></symbol>
  </defs>
</svg>

<div class="canvas">
<div class="stage">

  <!-- Splash -->
  <section class="screen" style="left:46px;top:39px;">
    <div class="brand" style="top:232px;font-size:48px;">Varelko</div>
  </section>

  <!-- Create profile -->
  <section class="screen" style="left:334px;top:39px;">
    <div class="status"><span>9:41</span><svg><use href="#i-status"/></svg></div>
    <div class="brand" style="top:48px;font-size:27px;">Varelko</div>
    <div class="title" style="top:108px;">Create Your Profile</div>
    <div class="label" style="top:141px;">Username</div><div class="field" style="top:155px;">Enter your username...</div>
    <div class="label" style="top:182px;">Email</div><div class="field" style="top:196px;">Enter your Email ID...</div>
    <div class="label" style="top:223px;">Password</div><div class="field" style="top:237px;">Enter your password...</div>
    <div class="label" style="top:264px;">Confirm Password</div><div class="field" style="top:278px;">Confirm your password...</div>
    <div class="divider" style="top:314px;">OR</div>
    <div class="social" style="left:32px;width:194px;top:337px;"><span class="dot"></span>Continue with Glimmo</div>
    <div class="social" style="left:32px;width:194px;top:369px;"><span class="dot"></span>Continue with Orchard</div>
    <div class="btn" style="top:418px;">Create profile</div>
    <svg class="tabbar" style="top:540px;height:13px" viewBox="0 0 256 13"><rect x="83" y="6" width="90" height="3" rx="1.5" fill="#555"/></svg>
  </section>

  <!-- Login -->
  <section class="screen" style="left:622px;top:39px;">
    <div class="status"><span>9:41</span><svg><use href="#i-status"/></svg></div>
    <div class="brand" style="top:48px;font-size:27px;">Varelko</div>
    <div class="title" style="top:106px;">Login</div>
    <div class="label" style="top:153px;">Username or Email ID</div><div class="field" style="top:167px;left:36px;">Enter your username or Email ID...</div>
    <div class="label" style="top:194px;">Password</div><div class="field" style="top:208px;left:36px;">Enter your password...</div>
    <div class="divider" style="top:260px;">OR</div>
    <div class="social" style="left:36px;width:194px;top:293px;"><span class="dot"></span>Continue with Glimmo</div>
    <div class="social" style="left:36px;width:194px;top:325px;">Continue with Orchard</div>
    <div class="btn" style="top:378px;">Login</div>
    <svg class="tabbar" style="top:540px;height:13px" viewBox="0 0 256 13"><rect x="83" y="6" width="90" height="3" rx="1.5" fill="#555"/></svg>
  </section>

  <!-- Timer dashboard -->
  <section class="screen" style="left:46px;top:636px;">
    <div class="status"><span>9:41</span><svg><use href="#i-status"/></svg></div>
    <div class="title">Timer</div>
    <svg class="icon" style="left:94px;top:98px;width:68px;height:68px;"><use href="#i-timer"/></svg>
    <div class="time-card" style="top:185px;"><div class="big">10:00<small>AM</small></div><div class="days">Mon, tue, wed, thu, fri</div></div>
    <div class="time-card" style="top:278px;"><div class="big">05:00<small>PM</small></div><div class="days">Mon, tue, wed, thu, fri</div></div>
    <div class="select" style="left:42px;top:407px;width:180px;">Preset 1<svg class="caret"><use href="#i-caret"/></svg></div>
    <div class="plus" style="top:446px;"><svg><use href="#i-plus"/></svg></div>
    <svg class="tabbar" viewBox="0 0 256 60"><path d="M0 20H32A26 26 0 0 0 84 20H256V60H0Z" fill="var(--amber)"/><circle cx="58" cy="18" r="15" fill="var(--amber)"/><use href="#i-timer" x="48" y="8" width="20" height="20" color="#1B1B1B"/><use href="#i-siren" x="119" y="26" width="18" height="18" color="#1B1B1B"/><use href="#i-speaker" x="187" y="26" width="18" height="18" color="#1B1B1B"/><rect x="83" y="50" width="90" height="3" rx="1.5" fill="#555"/></svg>
  </section>

  <!-- Timer add -->
  <section class="screen" style="left:334px;top:636px;">
    <div class="status"><span>9:41</span><svg><use href="#i-status"/></svg></div>
    <div class="title">Timer</div>
    <svg class="close"><use href="#i-close"/></svg>
    <div class="caption" style="top:85px;">Select Time</div>
    <div class="picker">
      <div class="digits"><span>10</span>:<span>10</span></div>
      <div class="ampm">AM<br>PM</div>
      <svg viewBox="-58 -58 116 116">
        <circle r="56" fill="var(--amber)"/>
        <g font-size="7" text-anchor="middle" dominant-baseline="middle" font-family="Roboto,sans-serif" fill="#1B1B1B">
          <text x="0" y="-45">12</text><text x="22.5" y="-39">1</text><text x="39" y="-22.5">2</text><text x="45" y="0">3</text><text x="39" y="22.5">4</text><text x="22.5" y="39">5</text><text x="0" y="45">6</text><text x="-22.5" y="39">7</text><text x="-39" y="22.5">8</text><text x="-45" y="0">9</text><text x="-39" y="-22.5">10</text><text x="-22.5" y="-39">11</text>
        </g>
        <line x1="0" y1="0" x2="-36" y2="-21" stroke="#1B1B1B" stroke-width="1.4"/><circle r="2" fill="#1B1B1B"/>
      </svg>
    </div>
    <div class="caption" style="top:299px;">Select Days of Week</div>
    <div class="days-row"><span class="chip">Sun</span><span class="chip on">Mon</span><span class="chip on">Tue</span><span class="chip on">Wed</span><span class="chip on">Thu</span><span class="chip on">Fri</span><span class="chip">Sat</span></div>
    <div class="btn" style="top:362px;">Add Time</div>
    <svg class="tabbar" viewBox="0 0 256 60"><path d="M0 20H32A26 26 0 0 0 84 20H256V60H0Z" fill="var(--amber)"/><circle cx="58" cy="18" r="15" fill="var(--amber)"/><use href="#i-timer" x="48" y="8" width="20" height="20" color="#1B1B1B"/><use href="#i-siren" x="119" y="26" width="18" height="18" color="#1B1B1B"/><use href="#i-speaker" x="187" y="26" width="18" height="18" color="#1B1B1B"/><rect x="83" y="50" width="90" height="3" rx="1.5" fill="#555"/></svg>
  </section>

  <!-- Motorised siren dashboard -->
  <section class="screen" style="left:46px;top:1241px;">
    <div class="status"><span>9:41</span><svg><use href="#i-status"/></svg></div>
    <div class="title">Motorised Siren</div>
    <div class="glow" style="top:97px;"><svg><use href="#i-siren"/></svg><p>Tap here!!</p></div>
    <div class="select" style="left:42px;top:242px;width:172px;">Motorised siren 1<svg class="caret"><use href="#i-caret"/></svg></div>
    <div class="plus" style="top:446px;"><svg><use href="#i-plus"/></svg></div>
    <svg class="tabbar" viewBox="0 0 256 60"><path d="M0 20H102A26 26 0 0 0 154 20H256V60H0Z" fill="var(--amber)"/><circle cx="128" cy="18" r="15" fill="var(--amber)"/><use href="#i-timer" x="49" y="26" width="18" height="18" color="#1B1B1B"/><use href="#i-siren" x="118" y="8" width="20" height="20" color="#1B1B1B"/><use href="#i-speaker" x="187" y="26" width="18" height="18" color="#1B1B1B"/><rect x="83" y="50" width="90" height="3" rx="1.5" fill="#555"/></svg>
  </section>

  <!-- Add motorised siren -->
  <section class="screen" style="left:334px;top:1241px;">
    <div class="status"><span>9:41</span><svg><use href="#i-status"/></svg></div>
    <div class="title">Add Motorised Siren</div>
    <svg class="close"><use href="#i-close"/></svg>
    <svg class="icon" style="left:97px;top:80px;width:64px;height:64px;"><use href="#i-siren"/></svg>
    <div class="label" style="top:172px;">Device name</div><div class="field" style="top:186px;">Enter Device name...</div>
    <div class="label" style="top:213px;">Device ID</div><div class="field" style="top:227px;">Enter device ID...</div>
    <div class="label" style="top:254px;">Location of device</div><div class="field" style="top:268px;">Enter location of the device...</div>
    <div class="label" style="top:295px;">Select a group</div>
    <div class="select left" style="left:32px;top:309px;width:194px;">Device group 1<svg class="caret"><use href="#i-caret"/></svg></div>
    <div class="btn" style="top:383px;">Add Now</div>
    <svg class="tabbar" viewBox="0 0 256 60"><path d="M0 20H102A26 26 0 0 0 154 20H256V60H0Z" fill="var(--amber)"/><circle cx="128" cy="18" r="15" fill="var(--amber)"/><use href="#i-timer" x="49" y="26" width="18" height="18" color="#1B1B1B"/><use href="#i-siren" x="118" y="8" width="20" height="20" color="#1B1B1B"/><use href="#i-speaker" x="187" y="26" width="18" height="18" color="#1B1B1B"/><rect x="83" y="50" width="90" height="3" rx="1.5" fill="#555"/></svg>
  </section>

  <!-- Headline -->
  <div class="headline">App UI Design for</div>
  <div class="hero-name">Varelko</div>

  <!-- Speaker dashboard -->
  <section class="screen" style="left:46px;top:1861px;">
    <div class="status"><span>9:41</span><svg><use href="#i-status"/></svg></div>
    <div class="title">Speaker</div>
    <div class="glow" style="top:92px;"><svg><use href="#i-speaker"/></svg><p>Tap here!!</p></div>
    <div class="select" style="left:42px;top:242px;width:172px;">Audio group 1<svg class="caret"><use href="#i-caret"/></svg></div>
    <div class="tile" style="left:41px;"><svg><use href="#i-note"/></svg><div>Upload mp3</div></div>
    <div class="tile" style="left:102px;"><svg><use href="#i-mic"/></svg><div>Record audio</div></div>
    <div class="tile" style="left:163px;"><svg><use href="#i-tts"/></svg><div>Text to speech</div></div>
    <div class="plus" style="top:446px;"><svg><use href="#i-plus"/></svg></div>
    <svg class="tabbar" viewBox="0 0 256 60"><path d="M0 20H170A26 26 0 0 0 222 20H256V60H0Z" fill="var(--amber)"/><circle cx="196" cy="18" r="15" fill="var(--amber)"/><use href="#i-timer" x="49" y="26" width="18" height="18" color="#1B1B1B"/><use href="#i-siren" x="119" y="26" width="18" height="18" color="#1B1B1B"/><use href="#i-speaker" x="186" y="8" width="20" height="20" color="#1B1B1B"/><rect x="83" y="50" width="90" height="3" rx="1.5" fill="#555"/></svg>
  </section>

  <!-- Upload mp3 -->
  <section class="screen" style="left:334px;top:1861px;">
    <div class="status"><span>9:41</span><svg><use href="#i-status"/></svg></div>
    <div class="title">Upload mp3 file</div>
    <svg class="close"><use href="#i-close"/></svg>
    <svg class="icon" style="left:104px;top:140px;width:50px;height:50px;"><use href="#i-note"/></svg>
    <div class="browse">Browse from device<svg><use href="#i-upload"/></svg></div>
    <svg class="wave"><use href="#i-wave"/></svg>
    <div class="file">sound1.mp3</div>
    <div class="btn" style="top:327px;">Upload</div>
    <svg class="tabbar" viewBox="0 0 256 60"><path d="M0 20H170A26 26 0 0 0 222 20H256V60H0Z" fill="var(--amber)"/><circle cx="196" cy="18" r="15" fill="var(--amber)"/><use href="#i-timer" x="49" y="26" width="18" height="18" color="#1B1B1B"/><use href="#i-siren" x="119" y="26" width="18" height="18" color="#1B1B1B"/><use href="#i-speaker" x="186" y="8" width="20" height="20" color="#1B1B1B"/><rect x="83" y="50" width="90" height="3" rx="1.5" fill="#555"/></svg>
  </section>

  <!-- Record audio -->
  <section class="screen" style="left:622px;top:1861px;">
    <div class="status"><span>9:41</span><svg><use href="#i-status"/></svg></div>
    <div class="title">Record Audio</div>
    <svg class="close"><use href="#i-close"/></svg>
    <div class="mic-ring"><svg><use href="#i-mic"/></svg></div>
    <div class="note">Tap to record.</div>
    <svg class="wave"><use href="#i-wave"/></svg>
    <div class="file">Recording1.aac</div>
    <div class="btn" style="top:327px;">Send to speaker</div>
    <svg class="tabbar" viewBox="0 0 256 60"><path d="M0 20H170A26 26 0 0 0 222 20H256V60H0Z" fill="var(--amber)"/><circle cx="196" cy="18" r="15" fill="var(--amber)"/><use href="#i-timer" x="49" y="26" width="18" height="18" color="#1B1B1B"/><use href="#i-siren" x="119" y="26" width="18" height="18" color="#1B1B1B"/><use href="#i-speaker" x="186" y="8" width="20" height="20" color="#1B1B1B"/><rect x="83" y="50" width="90" height="3" rx="1.5" fill="#555"/></svg>
  </section>

  <!-- Text to speech -->
  <section class="screen" style="left:910px;top:1861px;">
    <div class="status"><span>9:41</span><svg><use href="#i-status"/></svg></div>
    <div class="title">Text to Speech</div>
    <svg class="close"><use href="#i-close"/></svg>
    <svg class="icon" style="left:102px;top:80px;width:52px;height:52px;"><use href="#i-tts"/></svg>
    <div class="textbox">Hello everyone,<br>this is to inform you all that this message is being sent as a mock drill...</div>
    <svg class="wave" style="top:314px;"><use href="#i-wave"/></svg>
    <div class="keyboard">
      <div class="suggest"><span class="pick">“The”</span><span>the</span><span>to</span></div>
      <div class="krow"><span class="key">q</span><span class="key">w</span><span class="key">e</span><span class="key">r</span><span class="key">t</span><span class="key">y</span><span class="key">u</span><span class="key">i</span><span class="key">o</span><span class="key">p</span></div>
      <div class="krow"><span class="key">a</span><span class="key">s</span><span class="key">d</span><span class="key">f</span><span class="key">g</span><span class="key">h</span><span class="key">j</span><span class="key">k</span><span class="key">l</span></div>
      <div class="krow"><span class="key fn">⇧</span><span class="key">z</span><span class="key">x</span><span class="key">c</span><span class="key">v</span><span class="key">b</span><span class="key">n</span><span class="key">m</span><span class="key fn">⌫</span></div>
      <div class="krow"><span class="key fn wide">ABC</span><span class="key space">space</span><span class="key fn wide">return</span></div>
      <svg class="kbottom" viewBox="0 0 256 30"><circle cx="22" cy="12" r="7" fill="none" stroke="#555" stroke-width="1.2"/><path d="M18.5 13.5a4 4 0 0 0 7 0" fill="none" stroke="#555" stroke-width="1.2"/><use href="#i-mic" x="226" y="4" width="16" height="16" color="#555"/><rect x="82" y="24" width="92" height="3" rx="1.5" fill="#111"/></svg>
    </div>
  </section>

  <!-- Add speaker -->
  <section class="screen" style="left:1198px;top:1861px;">
    <div class="status"><span>9:41</span><svg><use href="#i-status"/></svg></div>
    <div class="title">Add Speaker</div>
    <svg class="close"><use href="#i-close"/></svg>
    <svg class="icon" style="left:94px;top:82px;width:68px;height:68px;"><use href="#i-speaker"/></svg>
    <div class="label" style="top:170px;">Device name</div><div class="field" style="top:184px;">Enter Device name...</div>
    <div class="label" style="top:211px;">Device ID</div><div class="field" style="top:225px;">Enter device ID...</div>
    <div class="label" style="top:252px;">Location of device</div><div class="field" style="top:266px;">Enter location of the device...</div>
    <div class="label" style="top:293px;">Select a group</div>
    <div class="select left" style="left:32px;top:307px;width:194px;">Device group 1<svg class="caret"><use href="#i-caret"/></svg></div>
    <div class="btn" style="top:383px;">Add Now</div>
    <svg class="tabbar" viewBox="0 0 256 60"><path d="M0 20H170A26 26 0 0 0 222 20H256V60H0Z" fill="var(--amber)"/><circle cx="196" cy="18" r="15" fill="var(--amber)"/><use href="#i-timer" x="49" y="26" width="18" height="18" color="#1B1B1B"/><use href="#i-siren" x="119" y="26" width="18" height="18" color="#1B1B1B"/><use href="#i-speaker" x="186" y="8" width="20" height="20" color="#1B1B1B"/><rect x="83" y="50" width="90" height="3" rx="1.5" fill="#555"/></svg>
  </section>

</div>
</div>
</body>
</html>
```